Bandbanner für Melodic Metal Band
Zielgruppe
Velvet Harbor ist eine Melodic Metal Band.
Wir brauchen ein neues Design für Backdrops (Bandbanner) die wir in verschiedenen Grössen drucken könnten.
(Bisher hatten wir die Grössen 500 cm x 300 cm, 400 cm x 250 cm und 200 cm x 200 cm)
Unser Bandlogo soll modern und inspiriert rüberkommen, um unsere Musik und Show zusätzlich zu unterstreichen.
Aufgabenstellung
- das Bandlogo soll stylisch und cool präsentiert sein (z.B. mit zusätzlichen Elementen ergänzt, umspielt, umrahmt... )
- einzigartig, Blickfang, auf uns zugeschnitten
- Das Design soll neu und neutral sein. Also nicht direkt bezogen auf eines unserer Alben. Wir möchten es für verschiedene Zwecke und für längere Zeit benutzen können
- modern, cool, vielleicht frech, kann Farben enthalten, hell/dunkel, mystisch
- soll zu unserem ganzen Auftreten und Style passen
- unsere Musik und Inhalte sind melodiös, modern, mal hart, mal sanfter, mal etwas dunkler, anklagend oder nachdenklich aber immer mit einer Prise Helligkeit und Hoffnung, nicht destruktiv. Deshalb nicht zu morbide oder zu klischeehaft, aber es darf gerne mysteriös oder melancholisch oder auch schlicht und speziell sein
(Das Logo und Sign könnten wir übrigens als AI, CDR, EPS, JPG, PDF, PNG und PSD zur Verfügung stellen).

```html
<!DOCTYPE html>
<html lang="de">
<head>
<meta charset="utf-8">
<title>Velvet Harbor – Backdrop</title>
<link rel="stylesheet" href="https://fonts.googleapis.com/css2?family=Cinzel:wght@700&family=Cormorant+Garamond:wght@500&display=swap">
<style>
  :root {
    --space-black: #0d0c09;
    --nebula-olive: #3a3524;
    --nebula-dust: #8a7d5e;
    --nebula-glow: #d9d2bd;
    --chrome: #d6d4cf;
    --ink-white: #f4f2ec;
  }
  html, body {
    margin: 0;
    padding: 0;
    width: 1200px;
    height: 675px;
    overflow: hidden;
    background: var(--space-black);
  }
  .backdrop {
    position: relative;
    width: 1200px;
    height: 675px;
    overflow: hidden;
    background: var(--space-black);
  }
  .nebula-field {
    position: absolute;
    inset: 0;
    background:
      radial-gradient(ellipse 260px 200px at 300px 200px, rgba(217,210,189,0.35), transparent 70%),
      radial-gradient(ellipse 240px 300px at 760px 180px, rgba(217,210,189,0.30), transparent 70%),
      radial-gradient(ellipse 300px 200px at 600px 460px, rgba(138,125,94,0.35), transparent 70%),
      radial-gradient(ellipse 600px 420px at 600px 300px, var(--nebula-olive), transparent 75%),
      var(--space-black);
  }
  .band-name {
    position: absolute;
    left: 0;
    right: 0;
    top: 282px;
    margin: 0;
    text-align: center;
    font-family: "Cinzel", serif;
    font-weight: 700;
    font-size: 104px;
    line-height: 1;
    letter-spacing: 4px;
    color: var(--chrome);
  }
  .band-sign {
    position: absolute;
    left: 0;
    right: 0;
    top: 532px;
    display: flex;
    justify-content: center;
    align-items: center;
    gap: 12px;
  }
  .band-sign__ring {
    width: 30px;
    height: 30px;
    border: 2px solid var(--ink-white);
    border-radius: 50%;
  }
  .band-sign__name {
    font-family: "Cinzel", serif;
    font-weight: 700;
    font-size: 20px;
    letter-spacing: 2px;
    color: var(--ink-white);
  }
  .social-row {
    position: absolute;
    left: 859px;
    top: 606px;
    display: flex;
    align-items: baseline;
    gap: 10px;
    font-family: "Cormorant Garamond", serif;
    font-weight: 500;
    font-size: 15px;
    color: var(--ink-white);
  }
  .social-row__handle { margin-right: 4px; }
</style>
</head>
<body>
  <main class="backdrop">
    <div class="nebula-field" role="img" aria-label="Dunkler Sternennebel in Oliv- und Goldtönen mit hellen Lichtwolken"></div>
    <h1 class="band-name">VELVET HARBOR</h1>
    <div class="band-sign">
      <span class="band-sign__ring"></span>
      <span class="band-sign__name">Velvet Harbor</span>
    </div>
    <nav class="social-row">
      <span class="social-row__handle">VelvetHarbor/</span>
      <span>Fanwall</span>
      <span>Chirper</span>
      <span>Pictora</span>
      <span>Streamly</span>
    </nav>
  </main>
</body>
</html>
```